Business cards to launch an education platform

Hi,
I am looking at having new business cards designed.
I am a startup, developing a web platform for schools and university, the education world. It's an online assessment system.
I would like a card that looks classy, and that is using the colors and the font of my logo.

I have attached:
1) my logo
2) A business card that I have designed quickly so you can have all the information required in the card, but I really don't like it.
3) The font that I am using (Lato Regular) to design my web platform
4) Some screenshots of my web platform so you can have a look at the style that I have.

Target Market(s)

Major market: Education system: Schools and university
Minor markets: Business in general

Industry/Entity Type

Business

Contact Information for Business Card

Clara Fenwick
Director

M: 0437 518 902
E: clara.fenwick@amberLoomSystems.com.au

Requirements
Must have
• The colors of my logo

```html
<!DOCTYPE html>
<html lang="en">
<head>
<meta charset="utf-8">
<title>Amber Loom Systems – Business Cards</title>
<link href="https://fonts.googleapis.com/css2?family=Lato:wght@400;700&display=swap" rel="stylesheet">
<style>
  :root {
    --navy: #004275;
    --sky: #1aa3dd;
    --white: #ffffff;
    --ink: #1c1c1c;
    --backdrop: #eceae7;
  }
  * { margin: 0; padding: 0; box-sizing: border-box; }
  html, body { width: 1200px; height: 900px; overflow: hidden; }
  body {
    position: relative;
    background: var(--backdrop);
    font-family: "Lato", sans-serif;
  }
  .card {
    position: absolute;
    border-radius: 14px;
    overflow: hidden;
    box-shadow: 0 4px 14px rgba(0,0,0,0.12);
  }
  /* Front */
  .card--front {
    left: 78px; top: 35px;
    width: 588px; height: 363px;
    background: var(--white);
  }
  .card--front .band {
    position: absolute; top: 28px; height: 100px;
    background: var(--navy);
  }
  .card--front .band--left { left: 0; width: 210px; }
  .card--front .band--right { left: 367px; width: 221px; }
  .brand-square {
    position: absolute;
    width: 84px; height: 84px;
  }
  .card--front .brand-square { left: 252px; top: 36px; background: var(--navy); }
  .brand-name {
    position: absolute;
    left: 0; width: 100%;
    text-align: center;
    font-weight: 400;
    line-height: 1;
  }
  .brand-name .line1 { display: block; font-size: 40px; letter-spacing: 3px; }
  .brand-name .line2 { display: block; font-size: 29px; letter-spacing: 2.5px; margin-top: 8px; }
  .card--front .brand-name { top: 160px; color: var(--navy); padding-left: 0; left: -12px; }
  .contact-person {
    position: absolute; left: 32px; top: 278px;
  }
  .contact-person .name { font-size: 22px; color: var(--navy); line-height: 1.1; }
  .contact-person .role { font-size: 16px; color: var(--ink); }
  .contact-lines {
    position: absolute; right: 36px; top: 276px;
    text-align: right; font-size: 16.5px; color: var(--ink);
  }
  .contact-lines .row { display: flex; align-items: center; justify-content: flex-end; gap: 10px; height: 25px; }
  .contact-lines svg { width: 13px; height: 13px; fill: var(--navy); }
  /* Back */
  .card--back {
    left: 390px; top: 505px;
    width: 565px; height: 350px;
    background: var(--navy);
  }
  .card--back .band {
    position: absolute; top: 80px; height: 115px;
    background: var(--white);
  }
  .card--back .band--left { left: 0; width: 208px; }
  .card--back .band--right { left: 357px; width: 208px; }
  .card--back .brand-square { left: 240px; top: 96px; background: var(--white); }
  .card--back .brand-name { top: 216px; color: var(--white); left: 7px; }
  .card--back .brand-name .line1 { font-size: 38px; }
  .card--back .brand-name .line2 { font-size: 27px; }
</style>
</head>
<body>
  <section class="card card--front" aria-label="Business card front">
    <div class="band band--left"></div>
    <div class="band band--right"></div>
    <div class="brand-square" aria-hidden="true"></div>
    <h1 class="brand-name"><span class="line1">AMBER LOOM</span><span class="line2">Systems</span></h1>
    <div class="contact-person">
      <p class="name">Clara Fenwick</p>
      <p class="role">Director</p>
    </div>
    <div class="contact-lines">
      <p class="row">0437 518 902
        <svg viewBox="0 0 24 24" aria-hidden="true"><path d="M6.6 10.8c1.4 2.8 3.8 5.1 6.6 6.6l2.2-2.2c.3-.3.7-.4 1-.2 1.1.4 2.3.6 3.6.6.6 0 1 .4 1 1V20c0 .6-.4 1-1 1C10.6 21 3 13.4 3 4c0-.6.4-1 1-1h3.5c.6 0 1 .4 1 1 0 1.3.2 2.5.6 3.6.1.3 0 .7-.2 1l-2.3 2.2z"/></svg>
      </p>
      <p class="row">clara.fenwick@amberLoomSystems.com.au
        <svg viewBox="0 0 24 24" aria-hidden="true"><path d="M2 5h20v14H2z M3.5 6.5v.6l8.5 5.6 8.5-5.6v-.6z" fill-rule="evenodd"/></svg>
      </p>
    </div>
  </section>

  <section class="card card--back" aria-label="Business card back">
    <div class="band band--left"></div>
    <div class="band band--right"></div>
    <div class="brand-square" aria-hidden="true"></div>
    <h2 class="brand-name"><span class="line1">AMBER LOOM</span><span class="line2">Systems</span></h2>
  </section>
</body>
</html>
```